Business Cards for a law firm

Business cards for our law firm. Use our silhoette logo and OAK PARTNERS - check our website (www.oakpartners.example)

Contact Information for Business Card

our silhouette logo, OAK PARTNERS, 800-555-0147, Dorian Pemberton, dorian@oakpartners.example

Requirements
Must have
• our silhouette logo, OAK PARTNERS, 800-555-0147, Dorian Pemberton, dorian@oakpartners.example

```html
<!DOCTYPE html>
<html lang="en">
<head>
<meta charset="utf-8">
<title>Oak Partners – Business Cards</title>
<link rel="stylesheet" href="https://fonts.googleapis.com/css2?family=Tenor+Sans&family=Arimo:wght@400&display=swap">
<style>
  :root {
    --bg: #dcdcdc;
    --paper: #f5f5f6;
    --navy: #1a2f68;
    --navy-band: #1d3275;
    --ink: #222222;
    --slate: #555555;
    --white: #ffffff;
  }
  * { margin: 0; padding: 0; box-sizing: border-box; }
  html, body { width: 1200px; height: 1040px; overflow: hidden; background: var(--bg); }
  .canvas { position: relative; width: 1200px; height: 1040px; }

  .card {
    position: absolute;
    border-radius: 18px;
    overflow: hidden;
  }
  .card-front {
    left: 285px; top: 130px; width: 641px; height: 366px;
    background: var(--paper);
  }
  .card-back {
    left: 284px; top: 568px; width: 646px; height: 368px;
    background: var(--navy);
  }

  .brand {
    position: absolute;
    display: flex; align-items: center; gap: 12px;
    font-family: "Tenor Sans", sans-serif;
    letter-spacing: 0.12em;
    white-space: nowrap;
  }
  .brand-mark { display: block; }
  .front-brand { right: 42px; top: 82px; transform: translateY(-50%); color: var(--navy); font-size: 22px; }
  .front-brand .brand-mark { width: 14px; height: 14px; background: var(--navy); }
  .back-brand { left: 50%; top: 176px; transform: translate(-50%, -50%); color: var(--white); font-size: 34px; gap: 18px; }
  .back-brand .brand-mark { width: 22px; height: 22px; background: var(--white); }

  .holder-name {
    position: absolute; left: 45px; top: 234px;
    font-family: "Tenor Sans", sans-serif;
    font-variant: small-caps;
    font-size: 25px; letter-spacing: 0.06em;
    color: var(--navy);
  }
  .divider {
    position: absolute; left: 45px; top: 266px; width: 553px; height: 1px;
    background: var(--ink);
  }
  .contact {
    position: absolute; top: 280px;
    display: flex; align-items: center; gap: 7px;
    font-family: "Arimo", sans-serif; font-size: 16px; color: var(--ink);
  }
  .contact-phone { left: 45px; }
  .contact-email { right: 43px; }
  .contact svg { display: block; fill: var(--navy); }

  .footer-band { position: absolute; left: 0; bottom: 0; width: 641px; height: 50px; display: block; }
  .website {
    position: absolute; right: 40px; top: 330px;
    font-family: "Arimo", sans-serif; font-size: 16px; letter-spacing: 0.14em;
    color: var(--white);
  }
</style>
</head>
<body>
<main class="canvas">

  <section class="card card-front" aria-label="Business card front">
    <div class="brand front-brand">
      <span class="brand-mark"></span>
      <span class="brand-name">OAK PARTNERS</span>
    </div>

    <h1 class="holder-name">Dorian Pemberton</h1>
    <div class="divider"></div>

    <div class="contact contact-phone">
      <svg width="14" height="14" viewBox="0 0 24 24" aria-hidden="true">
        <path d="M6.6 10.8a15.1 15.1 0 0 0 6.6 6.6l2.2-2.2a1 1 0 0 1 1-.25 11.4 11.4 0 0 0 3.6.57 1 1 0 0 1 1 1V20a1 1 0 0 1-1 1A17 17 0 0 1 3 4a1 1 0 0 1 1-1h3.5a1 1 0 0 1 1 1c0 1.25.2 2.45.57 3.57a1 1 0 0 1-.25 1z"/>
      </svg>
      <span>800-555-0147</span>
    </div>

    <div class="contact contact-email">
      <span>dorian@oakpartners.example</span>
      <svg width="14" height="10" viewBox="0 0 14 10" aria-hidden="true">
        <rect x="0" y="0" width="14" height="10"/>
        <path d="M0.8 0.8 L7 5.6 L13.2 0.8" stroke="#f5f5f6" stroke-width="1.2" fill="none"/>
      </svg>
    </div>

    <svg class="footer-band" viewBox="0 0 641 50" aria-hidden="true">
      <polygon points="0,10 347,10 334,26 0,26" fill="#555555"/>
      <polygon points="371,0 641,0 641,50 0,50 0,38 346,38" fill="#1d3275"/>
      <polyline points="0,32 340,32 368,4" stroke="#ffffff" stroke-width="1.5" fill="none"/>
    </svg>
    <span class="website">www.oakpartners.example</span>
  </section>

  <section class="card card-back" aria-label="Business card back">
    <div class="brand back-brand">
      <span class="brand-mark"></span>
      <span class="brand-name">OAK PARTNERS</span>
    </div>
  </section>

</main>
</body>
</html>
```